Photography Business, Business Card

Looking for a unique cutting edge card that takes advantage of the latest printing technologies. Please review this site for all the options they office: https://glowprintly.com. If you can think it they can do it. And if you have an idea and do not know if they can do it, I will check into it.

Target Market(s)

People and places I took images of and future clients.

Industry/Entity Type

Photography

Contact Information for Business Card

Name, cell & email. Derek Holloway, dholloway@kpnvisuals.com, 312-748-2961

Colors

Designer to choose only greyscale colors for use in the design.

Requirements
Must have
• 100% cutting edge. Is so great, those I hand it to always show it to someone else. A piece of art.
Nice to have
• Blacks, silvers, greys, some red. Maybe other colors?

```html
<!DOCTYPE html>
<html lang="en">
<head>
<meta charset="utf-8">
<title>Derek Holloway Photography – Business Card</title>
<link rel="stylesheet" href="https://fonts.googleapis.com/css2?family=Open+Sans:wght@400;600;700&display=swap">
<style>
  :root {
    --backdrop: #b5b5b5;
    --card: #333333;
    --card-edge: #1c1c1c;
    --ink-dark: #0e0e0e;
    --ink-light: #ffffff;
    --ink-muted: #8c8c8c;
    --ghost: rgba(40, 40, 40, 0.55);
  }
  * { margin: 0; padding: 0; box-sizing: border-box; }
  html, body {
    width: 1075px; height: 1200px; overflow: hidden;
    background: var(--backdrop);
    font-family: "Open Sans", Arial, sans-serif;
  }
  .canvas { position: relative; width: 1075px; height: 1200px; }

  .card {
    position: absolute; left: 206px; width: 665px; height: 396px;
    background: var(--card);
    box-shadow: 3px 3px 0 var(--card-edge), 4px 5px 8px rgba(0,0,0,0.35);
    overflow: hidden;
  }
  .card--front { top: 187px; border-top-right-radius: 122px; }
  .card--back  { top: 637px; border-bottom-right-radius: 122px; }

  .ghost-mark {
    position: absolute; border-radius: 50%;
    background: radial-gradient(ellipse at center, var(--ghost) 0%, rgba(40,40,40,0) 70%);
  }
  .card--front .ghost-mark { left: 10px; top: 40px; width: 520px; height: 330px; }
  .card--back  .ghost-mark { left: 10px; top: 0; width: 560px; height: 340px; }

  .brand { position: absolute; text-align: right; }
  .brand__name {
    display: block; color: var(--ink-dark);
    font-weight: 600; font-size: 40px; letter-spacing: 0.5px; line-height: 1;
  }
  .brand__tag {
    display: block; margin-top: 8px; color: var(--ink-light);
    font-weight: 400; font-size: 13.5px; letter-spacing: 3px;
  }
  .card--front .brand { right: 43px; top: 108px; }
  .card--back .brand { right: 141px; top: 174px; }

  .holder {
    position: absolute; left: 35px; top: 245px;
    color: var(--ink-muted); font-weight: 600; font-size: 21px; letter-spacing: 0.3px;
  }
  .contact { position: absolute; left: 35px; top: 300px; list-style: none; }
  .contact li {
    display: flex; align-items: center; gap: 6px; height: 24px;
    color: var(--ink-muted); font-size: 17px;
  }
  .contact svg { width: 17px; height: 17px; fill: var(--ink-muted); flex: none; }

  .studio-mark {
    position: absolute; right: 47px; top: 320px;
    color: var(--ink-light); font-weight: 600; font-size: 38px; letter-spacing: 6px; line-height: 1;
  }
</style>
</head>
<body>
<main class="canvas">

  <section class="card card--front" aria-label="Card front">
    <div class="ghost-mark" role="img" aria-label="Faint oversized script monogram in the background"></div>
    <div class="brand">
      <span class="brand__name">Derek Holloway</span>
      <span class="brand__tag">PHOTOGRAPHY</span>
    </div>
    <h1 class="holder">DEREK HOLLOWAY</h1>
    <ul class="contact">
      <li>
        <svg viewBox="0 0 24 24" aria-hidden="true"><path d="M6.6 10.8a15.1 15.1 0 0 0 6.6 6.6l2.2-2.2a1 1 0 0 1 1-.25 11.4 11.4 0 0 0 3.6.57 1 1 0 0 1 1 1V20a1 1 0 0 1-1 1A17 17 0 0 1 3 4a1 1 0 0 1 1-1h3.5a1 1 0 0 1 1 1c0 1.25.2 2.45.57 3.6a1 1 0 0 1-.25 1z"/></svg>
        312-748-2961
      </li>
      <li>
        <svg viewBox="0 0 24 24" aria-hidden="true"><path d="M2 5h20v14H2z"/><path d="M3 6l9 7 9-7" fill="none" stroke="#333" stroke-width="2"/></svg>
        dholloway@kpnvisuals.com
      </li>
      <li>
        <svg viewBox="0 0 24 24" aria-hidden="true"><path d="M12 2a10 10 0 1 0 0 20 10 10 0 0 0 0-20zm6.9 6h-2.9a15.7 15.7 0 0 0-1.4-3.6A8 8 0 0 1 18.9 8zM12 4c.8 1.2 1.5 2.5 1.9 4h-3.8c.4-1.5 1.1-2.8 1.9-4zM4.3 14a8 8 0 0 1 0-4h3.3a16 16 0 0 0 0 4zm.8 2h2.9c.3 1.3.8 2.5 1.4 3.6A8 8 0 0 1 5.1 16zM8 8H5.1a8 8 0 0 1 4.3-3.6C8.8 5.5 8.4 6.7 8 8zm4 12c-.8-1.2-1.5-2.5-1.9-4h3.8c-.4 1.5-1.1 2.8-1.9 4zm2.3-6H9.7a14.6 14.6 0 0 1 0-4h4.6a14.6 14.6 0 0 1 0 4zm.3 5.6c.6-1.1 1.1-2.3 1.4-3.6h2.9a8 8 0 0 1-4.3 3.6zm1.8-5.6a16 16 0 0 0 0-4h3.3a8 8 0 0 1 0 4z"/></svg>
        www.dhollowayfoto.com
      </li>
    </ul>
    <div class="studio-mark">DHF</div>
  </section>

  <section class="card card--back" aria-label="Card back">
    <div class="ghost-mark" role="img" aria-label="Faint oversized script monogram in the background"></div>
    <div class="brand">
      <span class="brand__name">Derek Holloway</span>
      <span class="brand__tag">PHOTOGRAPHY</span>
    </div>
  </section>

</main>
</body>
</html>
```